Website update for Harborline Ledger Partners & Bookkeeping

Our website needs updating
www.harborlineledgerpartners.com
Here are some of our latest print pieces to use as a guide?
I have also attached our graphic identity guide which includes the Pantone colors

Target Market(s)

Insurance Agencies

Industry/Entity Type

Accounting

Number of Pages Required

5+ page

```html
<!DOCTYPE html>
<html lang="en">
<head>
<meta charset="utf-8">
<title>Harborline Ledger Partners &amp; Bookkeeping</title>
<link href="https://fonts.googleapis.com/css2?family=Open+Sans:wght@400;600;700&family=Varela+Round&display=swap" rel="stylesheet">
<style>
:root{
  --teal:#17b3a6;
  --teal-dark:#0e9589;
  --teal-deep:#0b7d73;
  --teal-light:#3fd0c2;
  --ink:#3c3c3c;
  --muted:#777;
  --hero-bg:#eef0f1;
  --white:#fff;
}
*{box-sizing:border-box;margin:0;padding:0}
html,body{width:1200px;height:2644px;overflow:hidden;background:var(--white)}
body{font-family:"Open Sans",Arial,sans-serif;color:var(--ink);position:relative}
a{color:inherit;text-decoration:none}

.site-header{height:108px;display:flex;justify-content:space-between;align-items:center;padding:0 110px 0 140px}
.brand{display:flex;align-items:center;gap:14px}
.brand-mark{width:40px;height:40px;border-radius:50%;background:var(--teal)}
.brand-name{font-weight:700;font-size:22px;color:var(--teal-dark);line-height:1.15;max-width:300px}
.contact-top{text-align:right;font-size:14px;color:var(--muted)}
.contact-top p{margin:6px 0}
.contact-top .phone{font-size:30px;font-weight:700;color:var(--teal-dark);margin-left:8px}
.contact-top .mail{font-size:20px;color:var(--teal);margin-left:8px}

.main-nav{height:40px;background:linear-gradient(var(--teal-light),var(--teal-dark));display:flex;align-items:center;padding-left:90px}
.main-nav a{color:var(--white);font-size:16px;font-weight:600;padding:0 24px;line-height:40px}
.main-nav a.active{background:rgba(255,255,255,.25)}

.hero{height:512px;background:var(--hero-bg);position:relative;overflow:hidden}
.hero-photo{position:absolute;right:0;top:0;width:620px;height:512px;background:linear-gradient(90deg,var(--hero-bg),#d9dcde 35%,#c8b9a8 70%,#b9a693)}
.hero-text{position:absolute;left:120px;top:120px;font-family:"Varela Round",Arial,sans-serif;color:#555}
.hero-text .line{font-size:34px;line-height:46px}
.hero-text .big{font-size:50px;color:var(--teal);font-weight:700}
.hero-text .line.last{font-size:56px;color:var(--teal);margin-top:10px}
.dots{position:absolute;left:0;right:0;bottom:30px;display:flex;justify-content:center;gap:10px}
.dots span{width:12px;height:12px;border-radius:50%;border:2px solid #bbb}
.dots span.on{background:#bbb}

.about{height:468px;text-align:center;padding-top:24px}
.section-title{font-family:"Varela Round",Arial,sans-serif;font-size:46px;color:var(--teal);font-weight:400}
.about .lead{font-size:17px;font-weight:600;color:#555;width:820px;margin:16px auto 0;line-height:26px}
.about .lead b{color:var(--teal-dark)}
.about .body{font-size:13px;color:var(--muted);width:980px;margin:22px auto 0;line-height:22px}
.btn{display:inline-block;background:var(--teal);color:var(--white);font-size:16px;font-weight:600;padding:12px 34px;margin-top:56px}

.how{height:340px;display:flex}
.how-photo{width:560px;height:340px;background:linear-gradient(120deg,#e6e8ea,#bfc4c9 50%,#6b6f76)}
.how-panel{flex:1;background:linear-gradient(90deg,var(--teal-dark),var(--teal-light));color:var(--white);padding:40px 60px 0 70px}
.how-panel h2{font-family:"Varela Round",Arial,sans-serif;font-size:50px;font-weight:400;margin-left:-40px}
.how-panel ul{list-style:none;margin-top:16px}
.how-panel li{font-size:13px;line-height:20px;margin-bottom:14px;padding-left:22px;position:relative}
.how-panel li::before{content:"";position:absolute;left:0;top:6px;width:8px;height:8px;background:var(--white);border-radius:50%}

.services{height:744px;padding-top:32px;text-align:center}
.card-row{display:flex;justify-content:center;gap:24px}
.card-row.first{margin-top:26px}
.card-row.second{margin-top:72px}
.card{width:240px;height:216px;display:flex;flex-direction:column}
.card-img{flex:1}
.card-label{height:56px;background:var(--teal);color:var(--white);font-size:14px;font-weight:700;display:flex;align-items:center;justify-content:center;padding:0 10px;line-height:17px}
.ph-a{background:linear-gradient(135deg,#f2e6d9,#c9a789)}
.ph-b{background:linear-gradient(135deg,#c9d6c2,#7f9272)}
.ph-c{background:linear-gradient(135deg,#eef1f3,#aab3bb)}
.ph-d{background:linear-gradient(135deg,#f4f6f8,#9fb6cc)}
.ph-e{background:linear-gradient(135deg,#f5f0ea,#d3c3b1)}
.ph-f{background:linear-gradient(135deg,#f0f2f4,#b7bec5)}
.ph-g{background:linear-gradient(135deg,#e8ebee,#8f979f)}

.newsletter{height:188px;background:#f3f3f3;text-align:center;padding-top:40px}
.newsletter h2{font-family:"Varela Round",Arial,sans-serif;font-size:34px;color:var(--teal);font-weight:400;letter-spacing:1px}
.newsletter p{font-size:14px;color:var(--muted);margin-top:8px}
.signup{width:400px;height:44px;margin:22px auto 0;display:flex;border:1px solid #cfcfcf;background:var(--white)}
.signup span{flex:1;text-align:left;padding-left:14px;line-height:42px;font-size:13px;color:#aaa}
.signup button{width:44px;border:0;background:var(--teal);display:flex;align-items:center;justify-content:center}

.site-footer{height:224px;background:var(--teal);color:var(--white);position:relative}
.footer-top{display:flex;justify-content:space-between;align-items:center;padding:44px 60px 0 80px}
.footer-nav a{font-size:12px;font-weight:600;margin-right:22px}
.social{display:flex;gap:14px}
.social span{width:40px;height:40px;border-radius:50%;border:2px solid var(--white)}
.footer-info{display:flex;gap:120px;padding:40px 0 0 80px;font-size:13px;align-items:center}
.footer-info div{display:flex;align-items:center;gap:10px}
.copyright{position:absolute;left:0;right:0;bottom:0;height:28px;background:var(--teal-deep);font-size:11px;text-align:center;line-height:28px}
</style>
</head>
<body>

<header class="site-header">
  <div class="brand">
    <span class="brand-mark"></span>
    <span class="brand-name">Harborline Ledger Partners &amp; Bookkeeping</span>
  </div>
  <div class="contact-top">
    <p>Call Us On: <span class="phone">203-555-0186</span></p>
    <p>Mail Us: <span class="mail">hello@harborlineledgerpartners.com</span></p>
  </div>
</header>

<nav class="main-nav">
  <a class="active" href="#">Home</a>
  <a href="#">About Us</a>
  <a href="#">Compare</a>
  <a href="#">Our Services</a>
  <a href="#">How it Works</a>
  <a href="#">Resources</a>
  <a href="#">Contact Us</a>
  <a href="#">Blog</a>
</nav>

<section class="hero">
  <div class="hero-photo" role="img" aria-label="Photo of a smiling professional woman wearing glasses"></div>
  <div class="hero-text">
    <div class="line"><span class="big">Learn</span> why HLP is the <span class="big">leading</span></div>
    <div class="line">remote bookkeeping firm for</div>
    <div class="line last">Independent agencies</div>
  </div>
  <div class="dots"><span class="on"></span><span></span><span></span></div>
</section>

<section class="about">
  <h2 class="section-title">About Our Company</h2>
  <p class="lead"><b>HLP</b> is a professional Accounting/Bookkeeping firm located in Connecticut dedicated exclusively to Independent Insurance Agencies.</p>
  <p class="body">After working in-house at agencies for many years, our founder launched the firm in 2011 to help independent insurance agencies manage their accounting and bookkeeping. Today the firm has a small staff in Connecticut who know every part of agency management system accounting, and we have added room for new clients. Call us to see how we fit your needs.</p>
  <a class="btn" href="#">Show More</a>
</section>

<section class="how">
  <div class="how-photo" role="img" aria-label="Photo of a smiling business team in suits"></div>
  <div class="how-panel">
    <h2>How it Works</h2>
    <ul>
      <li>Agencies scan documents to a secure shared folder, typically folding the process into an existing workflow.</li>
      <li>On an agreed-upon schedule our team creates checks in your system and notifies you that checks are ready to print. We can also process vendor and company payments via your bank's bill pay or ACH system.</li>
      <li>Daily communication with your staff and insurance company/broker accounting staff on billing issues, we don't interact with your customers.</li>
    </ul>
  </div>
</section>

<section class="services">
  <h2 class="section-title">Service Available</h2>
  <div class="card-row first">
    <div class="card"><div class="card-img ph-a" role="img" aria-label="Photo of a couple reviewing papers"></div><div class="card-label">RECORD DIRECT BILL COMMISSION</div></div>
    <div class="card"><div class="card-img ph-b" role="img" aria-label="Photo of banknotes"></div><div class="card-label">RECONCILE &amp; PAY AGENCY BILL PREMIUMS</div></div>
    <div class="card"><div class="card-img ph-c" role="img" aria-label="Photo of a calculator and ledger"></div><div class="card-label">RECONCILE GENERAL LEDGER ACCOUNTS</div></div>
    <div class="card"><div class="card-img ph-d" role="img" aria-label="Photo of financial charts on paper"></div><div class="card-label">PREPARE &amp; INTERPRET FINANCIAL STATEMENTS</div></div>
  </div>
  <div class="card-row second">
    <div class="card"><div class="card-img ph-e" role="img" aria-label="Photo of a paid invoice stamp"></div><div class="card-label">PAY VENDOR INVOICES</div></div>
    <div class="card"><div class="card-img ph-f" role="img" aria-label="Photo of a hand writing on documents"></div><div class="card-label">RECONCILE CUSTOMER ACCOUNTS RECEIVABLE</div></div>
    <div class="card"><div class="card-img ph-g" role="img" aria-label="Photo of a person typing on a laptop"></div><div class="card-label">PROCESS PAYROLL</div></div>
  </div>
</section>

<section class="newsletter">
  <h2>NEWSLETTER</h2>
  <p>Enter your e-mail address to receive regular updates, as well as news on upcoming events and special offers.</p>
  <div class="signup">
    <span>Enter Your E-mail</span>
    <button aria-label="Subscribe"><svg width="18" height="18" viewBox="0 0 18 18"><path d="M4 9h10M10 5l4 4-4 4" stroke="#fff" stroke-width="2" fill="none"/></svg></button>
  </div>
</section>

<footer class="site-footer">
  <div class="footer-top">
    <nav class="footer-nav">
      <a href="#">HOME</a><a href="#">ABOUT US</a><a href="#">COMPARE</a><a href="#">OUR SERVICES</a><a href="#">HOW IT WORKS</a><a href="#">RESOURCES</a><a href="#">CONTACT US</a><a href="#">BLOG</a>
    </nav>
    <div class="social"><span></span><span></span><span></span></div>
  </div>
  <div class="footer-info">
    <div>
      <svg width="16" height="22" viewBox="0 0 16 22"><path d="M8 1a7 7 0 0 0-7 7c0 5 7 13 7 13s7-8 7-13a7 7 0 0 0-7-7z" fill="#fff"/><circle cx="8" cy="8" r="2.5" fill="#17b3a6"/></svg>
      <span>HLP<br>42 Quay Street, Mystic, CT 06355</span>
    </div>
    <div>
      <svg width="18" height="18" viewBox="0 0 18 18"><path d="M4 1l3 4-2 2c1 2 3 4 5 5l2-2 4 3-2 3C8 16 2 10 1 4z" fill="#fff"/></svg>
      <span>203-555-0186</span>
    </div>
    <div>
      <svg width="20" height="14" viewBox="0 0 20 14"><rect x="1" y="1" width="18" height="12" fill="none" stroke="#fff" stroke-width="1.5"/><path d="M1 1l9 7 9-7" fill="none" stroke="#fff" stroke-width="1.5"/></svg>
      <span>hello@harborlineledgerpartners.com</span>
    </div>
  </div>
  <div class="copyright">© Harborline Ledger Partners &amp; Bookkeeping 2016. All Rights reserved.</div>
</footer>

</body>
</html>
```